Corporate Business Card

Very professional, Modern, Not to busy, include phone address email, website
(253) 617-4930, 18761 52nd Avenue S, Kent, WA 98047, martin@plumlinegroup.com, varkoworks.com

Target Market(s)

Manufacturing

Industry/Entity Type

Aero, machining, manufacturing, Off road racing

Contact Information for Business Card

Phone, address email, website

```html
<!DOCTYPE html>
<html lang="en">
<head>
<meta charset="utf-8">
<title>Varko Works – Business Card</title>
<link rel="stylesheet" href="https://fonts.googleapis.com/css2?family=Montserrat:wght@400;700;800&family=Arimo:wght@400&display=swap">
<style>
  :root {
    --navy: #17356f;
    --red: #d4212b;
    --paper: #f7f7f7;
    --ink: #222831;
    --stage: #2b2b2d;
  }
  * { margin: 0; padding: 0; box-sizing: border-box; }
  html, body { width: 1200px; height: 900px; overflow: hidden; }
  body {
    background: var(--stage);
    display: flex;
    flex-direction: column;
    align-items: center;
    justify-content: center;
    gap: 34px;
  }
  .card {
    position: relative;
    width: 700px;
    height: 400px;
    border-radius: 26px;
    overflow: hidden;
  }

  /* Back side */
  .card-back {
    background: var(--navy);
    display: flex;
    align-items: center;
    justify-content: center;
  }
  .wordmark {
    display: flex;
    align-items: center;
    gap: 16px;
    font-family: "Montserrat", sans-serif;
    font-weight: 800;
    text-transform: uppercase;
    letter-spacing: 2px;
  }
  .wordmark-square {
    width: 22px;
    height: 22px;
    background: var(--red);
  }
  .card-back .wordmark { font-size: 62px; color: #fff; }

  /* Front side */
  .card-front { background: var(--paper); }
  .card-front .wordmark {
    position: absolute;
    top: 52px;
    left: 56px;
    font-size: 38px;
    color: var(--navy);
    gap: 12px;
  }
  .card-front .wordmark-square { width: 15px; height: 15px; }
  .divider {
    position: absolute;
    top: 176px;
    left: 56px;
    right: 56px;
    height: 2px;
    background: var(--navy);
  }
  .contact {
    position: absolute;
    top: 198px;
    left: 56px;
    font-family: "Arimo", sans-serif;
    font-size: 17px;
    color: var(--ink);
    list-style: none;
    line-height: 1.35;
  }
  .contact-address { margin-bottom: 8px; }
  .contact-item {
    display: flex;
    align-items: center;
    gap: 9px;
    margin-bottom: 4px;
  }
  .contact-icon { width: 14px; height: 14px; flex: none; fill: var(--red); }
  .person {
    position: absolute;
    top: 196px;
    right: 56px;
    text-align: right;
    font-family: "Montserrat", sans-serif;
  }
  .person-name {
    font-size: 30px;
    font-weight: 700;
    letter-spacing: 1px;
    color: var(--navy);
    text-transform: uppercase;
  }
  .person-name .surname { color: var(--red); }
  .person-role {
    display: inline-block;
    margin-top: 4px;
    padding-top: 3px;
    border-top: 2px solid var(--navy);
    padding-left: 60px;
    font-size: 17px;
    font-weight: 400;
    letter-spacing: 1.5px;
    color: var(--ink);
  }
  .edge-band {
    position: absolute;
    left: 0; right: 0; bottom: 0;
    width: 700px;
    height: 16px;
  }
</style>
</head>
<body>

  <section class="card card-back" aria-label="Card back">
    <div class="wordmark"><span class="wordmark-square"></span>Varko Works</div>
  </section>

  <section class="card card-front" aria-label="Card front">
    <div class="wordmark"><span class="wordmark-square"></span>Varko Works</div>
    <div class="divider"></div>

    <ul class="contact">
      <li class="contact-address">18761 52nd Avenue S, Kent<br>WA 98047</li>
      <li class="contact-item">
        <svg class="contact-icon" viewBox="0 0 24 24" aria-hidden="true"><path d="M6.6 10.8a15.1 15.1 0 0 0 6.6 6.6l2.2-2.2a1 1 0 0 1 1-.25 11.4 11.4 0 0 0 3.6.57 1 1 0 0 1 1 1V20a1 1 0 0 1-1 1A17 17 0 0 1 3 4a1 1 0 0 1 1-1h3.5a1 1 0 0 1 1 1c0 1.25.2 2.45.57 3.57a1 1 0 0 1-.25 1z"/></svg>
        (253) 617-4930
      </li>
      <li class="contact-item">
        <svg class="contact-icon" viewBox="0 0 24 24" aria-hidden="true"><path d="M2 5h20v14H2z" opacity=".9"/><path d="M2 5l10 8 10-8" fill="none" stroke="#fff" stroke-width="2"/></svg>
        martin@plumlinegroup.com
      </li>
      <li class="contact-item">
        <svg class="contact-icon" viewBox="0 0 24 24" aria-hidden="true"><circle cx="12" cy="12" r="10"/><path d="M2 12h20M12 2c3 3 3 17 0 20M12 2c-3 3-3 17 0 20M4 7h16M4 17h16" fill="none" stroke="#fff" stroke-width="1.3"/></svg>
        www.varkoworks.com
      </li>
    </ul>

    <div class="person">
      <div class="person-name">Owen <span class="surname">Marsh</span></div>
      <div class="person-role">Owner</div>
    </div>

    <svg class="edge-band" viewBox="0 0 700 16" preserveAspectRatio="none" aria-hidden="true">
      <polygon points="0,0 300,0 284,16 0,16" fill="var(--navy)"/>
      <polygon points="312,0 700,0 700,16 296,16" fill="var(--red)"/>
    </svg>
  </section>

</body>
</html>
```